Home Security Company Business Card

Looking for a eye catching business card that is non traditional and stands out but yet still looks professional. It should include all the pertinent information such as name, title, address, telephone, e-mail, website address should definitely stand out and then finally the logo.

Target Market(s)

Residential and Commercial accounts mostly upscale accounts

Industry/Entity Type

Security

Contact Information for Business Card

Name
Title
Address
Office #
Cell #
E-mail
Website

Font styles to use
Serif
Sans Serif

Requirements
Must have
• Logo, two sided color configuration
Nice to have
• You decide
Should not have
• There really aren't any.

```html
<!DOCTYPE html>
<html lang="en">
<head>
<meta charset="utf-8">
<title>Ironvale Protection Group – Business Card</title>
<link href="https://fonts.googleapis.com/css2?family=Open+Sans:wght@400;600;700&display=swap" rel="stylesheet">
<style>
  :root {
    --backdrop: #5a4634;
    --crimson: #7c1416;
    --crimson-deep: #5e0d0f;
    --gold: #f2b63a;
    --gold-light: #ffe08a;
    --gold-deep: #c98a16;
    --white: #ffffff;
    --rule: #c99a73;
  }
  * { margin: 0; padding: 0; box-sizing: border-box; }
  html, body { width: 1200px; height: 750px; overflow: hidden; }
  body {
    background: var(--backdrop);
    font-family: "Open Sans", Arial, sans-serif;
    position: relative;
  }
  .card {
    position: absolute;
    top: 202px;
    width: 559px;
    height: 318px;
    border-radius: 18px;
    overflow: hidden;
    box-shadow: 0 6px 14px rgba(0,0,0,0.45);
  }
  .card--front { left: 28px; background: var(--crimson); }
  .card--back { left: 614px; background: var(--white); }

  .edge-accent {
    position: absolute;
    top: 0;
    height: 100%;
    width: 100px;
  }
  .card--front .edge-accent {
    right: 0;
    background: linear-gradient(90deg, var(--gold-deep), var(--gold-light) 45%, var(--gold) 75%, var(--crimson-deep));
  }
  .card--back .edge-accent {
    left: 0;
    background: linear-gradient(90deg, var(--crimson-deep), var(--crimson) 55%, var(--gold) 90%, var(--white));
  }

  .brand {
    position: absolute;
    display: flex;
    align-items: center;
    gap: 10px;
    font-weight: 700;
    white-space: nowrap;
  }
  .brand__mark { display: block; }
  .card--front .brand { left: 42px; top: 60px; color: var(--gold); font-size: 17px; }
  .card--front .brand__mark { width: 28px; height: 28px; background: var(--gold); }
  .card--back .brand { left: 150px; top: 128px; color: var(--crimson); font-size: 23px; }
  .card--back .brand__mark { width: 40px; height: 40px; border-radius: 50%; background: var(--crimson); }

  .holder { position: absolute; left: 42px; top: 156px; width: 420px; }
  .holder__name { color: var(--white); font-weight: 700; font-size: 23px; line-height: 1.1; }
  .holder__title {
    color: var(--gold);
    font-size: 15px;
    line-height: 1.2;
    padding-left: 2px;
    border-bottom: 1px solid var(--rule);
  }

  .contacts { position: absolute; left: 42px; top: 212px; list-style: none; }
  .contacts li {
    display: flex;
    align-items: center;
    gap: 8px;
    color: var(--white);
    font-size: 15.5px;
    line-height: 19.3px;
  }
  .contacts svg { width: 13px; height: 13px; fill: var(--gold); flex: none; }

  .website {
    position: absolute;
    left: 0; right: 0;
    top: 252px;
    padding-left: 82px;
    text-align: center;
    color: var(--crimson);
    font-weight: 700;
    font-size: 15.5px;
  }
</style>
</head>
<body>
  <section class="card card--front">
    <div class="edge-accent" role="img" aria-label="Gold decorative accent along the card edge"></div>
    <div class="brand"><span class="brand__mark"></span>Ironvale Protection Group</div>
    <div class="holder">
      <p class="holder__name">Daniel Hartwell</p>
      <p class="holder__title">Owner</p>
    </div>
    <ul class="contacts">
      <li><svg viewBox="0 0 16 16"><path d="M1 5c0-2 3-3 7-3s7 1 7 3v1h-4V5H5v1H1zm2 2h10l1 7H2z"/></svg>+330 5550-1842</li>
      <li><svg viewBox="0 0 16 16"><path d="M3 1l3 3-2 2c1 2 3 4 6 6l2-2 3 3-2 3C7 15 1 9 1 3z"/></svg>+3305550-27314</li>
      <li><svg viewBox="0 0 16 16"><path d="M1 3h14v10H1zm1.5 1.5L8 9l5.5-4.5V12h-11z" fill-rule="evenodd"/></svg>info@danielhartwellmail.com</li>
      <li><svg viewBox="0 0 16 16"><path d="M8 0a5 5 0 0 1 5 5c0 4-5 11-5 11S3 9 3 5a5 5 0 0 1 5-5zm0 3a2 2 0 1 0 0 4 2 2 0 0 0 0-4z" fill-rule="evenodd"/></svg>248 Harbor Lane Millbrook, Illinois 60999</li>
    </ul>
  </section>

  <section class="card card--back">
    <div class="edge-accent" role="img" aria-label="Crimson and gold decorative accent along the card edge"></div>
    <div class="brand"><span class="brand__mark"></span>Ironvale Protection Group</div>
    <p class="website">www.ironvaleprotectiongroup.com</p>
  </section>
</body>
</html>
```